Residential Remodeling Contractor needs updated business card

I need a new design for my business card.
Name of the company is Ridgefell Construction. I need a card that commands presence, strength, integrity. I have been in business for 28 years. I am a Residential Remodeling Contractor that covers all aspects of a residential remodel and build.

```html
<!DOCTYPE html>
<html lang="en">
<head>
<meta charset="utf-8">
<title>Ridgefell Construction – Business Card</title>
<link rel="stylesheet" href="https://fonts.googleapis.com/css2?family=Arimo:wght@400;700&display=swap">
<style>
  :root {
    --stage: #1c1c1e;
    --card-blue: #1b3f85;
    --card-blue-deep: #163672;
    --ink-white: #ffffff;
    --ink-soft: rgba(255, 255, 255, 0.88);
    --rule: rgba(255, 255, 255, 0.55);
  }
  * { box-sizing: border-box; margin: 0; padding: 0; }
  html, body {
    width: 1200px;
    height: 801px;
    overflow: hidden;
    background: var(--stage);
    font-family: "Arimo", Arial, sans-serif;
    color: var(--ink-white);
  }
  .stage {
    width: 1200px;
    height: 801px;
    display: flex;
    align-items: center;
    justify-content: center;
    gap: 40px;
  }
  .card {
    width: 540px;
    height: 309px;
    border-radius: 22px;
    background: linear-gradient(135deg, var(--card-blue) 0%, var(--card-blue-deep) 100%);
    position: relative;
    overflow: hidden;
  }

  /* Wordmark: plain name in the card's text face */
  .wordmark {
    display: flex;
    align-items: center;
    gap: 12px;
    font-weight: 700;
    text-transform: uppercase;
    color: var(--ink-white);
    line-height: 1.05;
  }
  .wordmark__square {
    flex: none;
    background: var(--ink-white);
  }

  /* Back: contact side */
  .card--back .wordmark {
    position: absolute;
    left: 40px;
    top: 128px;
    font-size: 22px;
    letter-spacing: 1.5px;
  }
  .card--back .wordmark__square { width: 16px; height: 16px; }
  .card--back .divider {
    position: absolute;
    left: 282px;
    top: 42px;
    width: 1px;
    height: 225px;
    background: var(--rule);
  }
  .contact {
    position: absolute;
    left: 304px;
    top: 52px;
    right: 20px;
  }
  .contact__name {
    font-weight: 700;
    font-size: 20px;
    letter-spacing: 0.5px;
    text-transform: uppercase;
  }
  .contact__role {
    font-size: 12.5px;
    color: var(--ink-soft);
    margin-top: 3px;
  }
  .contact__address {
    font-size: 12.5px;
    color: var(--ink-soft);
    line-height: 1.45;
    margin-top: 16px;
    font-style: normal;
  }
  .contact__lines {
    list-style: none;
    margin-top: 14px;
  }
  .contact__lines li {
    display: flex;
    align-items: center;
    gap: 7px;
    font-size: 12.5px;
    color: var(--ink-soft);
    line-height: 1.75;
  }
  .contact__lines svg { width: 11px; height: 11px; flex: none; fill: var(--ink-white); }

  /* Front: brand side */
  .card--front {
    display: flex;
    align-items: center;
    justify-content: center;
  }
  .card--front .wordmark {
    font-size: 34px;
    letter-spacing: 2px;
    gap: 16px;
  }
  .card--front .wordmark__square { width: 22px; height: 22px; }
</style>
</head>
<body>
<main class="stage">

  <section class="card card--back" aria-label="Business card, contact side">
    <div class="wordmark"><span class="wordmark__square"></span><span>Ridgefell<br>Construction</span></div>
    <span class="divider"></span>
    <div class="contact">
      <p class="contact__name">Marco Delvane</p>
      <p class="contact__role">Owner &amp; Manager</p>
      <address class="contact__address">P.O. Box&nbsp; Street Name<br>Country Name AB, A5B 521</address>
      <ul class="contact__lines">
        <li>
          <svg viewBox="0 0 24 24" aria-hidden="true"><path d="M6.6 10.8a15.2 15.2 0 0 0 6.6 6.6l2.2-2.2c.3-.3.7-.4 1-.2 1.1.4 2.3.6 3.6.6.6 0 1 .4 1 1V20c0 .6-.4 1-1 1A17 17 0 0 1 3 4c0-.6.4-1 1-1h3.5c.6 0 1 .4 1 1 0 1.3.2 2.5.6 3.6.1.3 0 .7-.2 1z"/></svg>
          555 214 7730
        </li>
        <li>
          <svg viewBox="0 0 24 24" aria-hidden="true"><path d="M2 5h20v14H2z M2 5l10 8 10-8" fill="none" stroke="#fff" stroke-width="2.4"/></svg>
          info@ridgefellconstruction.com
        </li>
        <li>
          <svg viewBox="0 0 24 24" aria-hidden="true"><circle cx="12" cy="12" r="9" fill="none" stroke="#fff" stroke-width="2.4"/><path d="M3 12h18M12 3c3 3 3 15 0 18M12 3c-3 3-3 15 0 18" fill="none" stroke="#fff" stroke-width="1.8"/></svg>
          www.ridgefellconstruction.com
        </li>
      </ul>
    </div>
  </section>

  <section class="card card--front" aria-label="Business card, brand side">
    <div class="wordmark"><span class="wordmark__square"></span><span>Ridgefell<br>Construction</span></div>
  </section>

</main>
</body>
</html>
```